Design website home page for pathology consulting company

Starting a new consulting company with anatomic pathologists focused on expert diagnosis and second opinions on difficult pathology cases. In the near future we will be incorporating next generation diagnostics for rare diseases of childhood into the business. These include discovery and testing of DNA for mutations.

The company is formed around one of the best known pathologists in the world named Marcel "Biscuit" Trowell. The name of the company is "BiscuitLab"

We had a logo design by SketchForum - it is great. I will attach file as soon as I have it (contest ending today). Our company is medical, uses microscopes, DNA, probably will focus on childhood diseases but not solely on childhood diseases. we're not particularly conservative, but the customers we want to appeal to include older practicing pathologists as well as patients (sometimes parents) looking for second opinions.

Think a group of expert doctors diagnosing disease through the microscope and through DNA technology, ages ranging from 35-75 all trained by the best pathologist in the world - "Biscuit"

We receive glass slides from diseases from patients all over the world from docs who need an expert to tell them what is the diagnosis. So "path to the diagnosis" is also part of the company marketing message.

We want the website design to describe our company but be very simple to find what one is looking for as we will use it as the launch page to:
1) order services
2) check results/reports
3) set up new account
4) speak with one of the pathologists
5) see our test menu
6) access our educational material/webinars
Updates

Update - looking for home page design and then finalists will ask for second page design to keep with theme - ok?

Reason: realized this project isn't web design but web home page design - thanks

Reason: Holidays for some in next two weeks

Reason: Hot discussion among collaborators for a few of the submissions. Will provide detail individually this weekend. Thanks so much for all the submissions!

Target Market(s)

Referring pathologists, physicians who want second opinions on pathology disease diagnosis, patients who have had biopsies (either patients themselves or parents of patients), generally high education level

Industry/Entity Type

Marketing

Requirements
Must have
• BiscuitLab
Next Generation Pathology Consultants

```html
<!DOCTYPE html>
<html lang="en">
<head>
<meta charset="utf-8">
<title>BiscuitLab – Next Generation Pathology Consultants</title>
<link href="https://fonts.googleapis.com/css2?family=Tinos&family=Ubuntu:wght@400;500&family=Open+Sans:wght@400;600&display=swap" rel="stylesheet">
<style>
:root{
  --blue:#0b63ad;
  --blue-dark:#0a4f8f;
  --ink:#333;
  --muted:#9a9a9a;
  --nav-grey:#dcdcdc;
  --paper:#efeeeb;
  --white:#fff;
  --footer:#0a0a0a;
  --rule:#cfcfcf;
}
*{box-sizing:border-box;margin:0;padding:0}
html,body{width:878px;height:1200px;overflow:hidden}
body{background:var(--paper);font-family:"Open Sans",sans-serif;color:var(--ink);position:relative}
.page{position:absolute;left:80px;top:18px;width:718px;height:1166px;background:var(--white)}
.abs{position:absolute}
.serif{font-family:"Tinos",serif;color:var(--blue);font-weight:400}

/* header */
.brand{left:14px;top:20px;display:flex;align-items:center;gap:8px}
.brand-mark{width:62px;height:62px;border-radius:50%;background:var(--blue)}
.brand-name{font-family:"Tinos",serif;color:var(--blue);font-size:24px;line-height:1;letter-spacing:.5px}
.brand-tag{font-family:"Tinos",serif;color:#777;font-size:7.5px;margin-top:3px}
.nav{left:267px;top:30px;display:flex;height:37px}
.nav a{width:87px;display:flex;align-items:center;justify-content:center;font-family:"Ubuntu",sans-serif;font-size:11.5px;color:#444;text-decoration:none;background:var(--nav-grey);border-left:1px solid #c9c9c9}
.nav a.active{background:var(--blue);color:var(--white);border-left:none}

/* hero */
.hero{left:0;top:97px;width:718px;height:349px;background:linear-gradient(90deg,#dfe4ea 0%,#c9d2dc 30%,#eef1f4 60%,#f6f7f8 100%)}
.hero-circle{left:469px;top:64px;width:224px;height:224px;border-radius:50%;background:rgba(255,255,255,.6);text-align:center;padding-top:50px}
.hero-title{font-size:36px;line-height:1}
.hero-sub{font-family:"Ubuntu",sans-serif;color:var(--blue);font-size:11px;line-height:14px;margin-top:12px}
.hero-text{font-family:"Ubuntu",sans-serif;color:#888;font-size:8.5px;line-height:11.5px;margin-top:8px}
.btn-pill{display:inline-block;margin-top:12px;background:var(--blue);color:var(--white);font-family:"Ubuntu",sans-serif;font-size:11px;padding:6px 10px;border-radius:14px}

/* band */
.band{left:0;top:446px;width:718px;height:86px;background:var(--blue);color:var(--white)}
.band h2{position:absolute;left:15px;top:12px;font-family:"Tinos",serif;font-weight:400;font-size:30px;letter-spacing:.5px}
.band p{position:absolute;left:15px;top:51px;font-size:9.2px;line-height:12px;font-weight:600;width:560px}
.learn{position:absolute;left:578px;top:28px;width:115px;height:30px;border-radius:15px;background:var(--white);display:flex;align-items:center;justify-content:flex-end;gap:9px;padding-right:12px;font-family:"Tinos",serif;color:var(--blue);font-size:13px}

/* features */
.feature{top:565px;width:220px}
.feature-icon{position:absolute;left:0;top:0;width:47px;height:47px;border-radius:50%;background:var(--blue-dark)}
.feature h3{position:absolute;left:60px;top:3px;font-size:14.5px;white-space:nowrap}
.feature p{position:absolute;left:61px;top:27px;width:150px;color:var(--muted);font-size:8.6px;line-height:11.5px}
.feature .more{position:absolute;left:62px;top:74px;font-family:"Ubuntu",sans-serif;font-size:9.5px;color:#222;text-decoration:underline}

.rule{left:0;width:718px;border-top:1px dashed var(--rule)}

/* welcome */
.welcome{left:15px;top:720px;width:500px}
.welcome h2{font-size:15px}
.welcome p{margin-top:8px;color:var(--muted);font-size:8.8px;line-height:13.3px}
.btn-square{position:absolute;background:var(--blue);color:var(--white);font-family:"Ubuntu",sans-serif;font-size:9.5px;display:flex;align-items:center;justify-content:center;border:1px solid var(--blue-dark)}
.signup{left:539px;top:720px;width:165px}
.signup h2{font-size:15px}
.field{position:absolute;left:1px;width:164px;height:23px;border:1px solid #ccc;font-size:8.5px;color:#999;padding:6px 7px}
.forgot{position:absolute;left:82px;top:122px;font-size:7px;color:#999;white-space:nowrap}

/* services */
.services-title{left:15px;top:903px;font-size:19.5px}
.service{top:927px;width:162px}
.service-photo{width:162px;height:100px}
.service h3{margin-top:11px;font-size:14.5px;line-height:17px}
.service p{margin-top:2px;color:var(--muted);font-size:8.6px;line-height:11.5px;width:150px}

/* footer */
.footer{left:0;top:1130px;width:718px;height:36px;background:var(--footer);color:var(--white);font-size:9px;display:flex;align-items:center;justify-content:space-between;padding:0 15px}
</style>
</head>
<body>
<div class="page">
  <header>
    <div class="abs brand">
      <div class="brand-mark"></div>
      <div>
        <div class="brand-name">BiscuitLab</div>
        <div class="brand-tag">Next Generation Pathology Consultants</div>
      </div>
    </div>
    <nav class="abs nav">
      <a class="active" href="#">Home</a>
      <a href="#">Physicians</a>
      <a href="#">Specialities</a>
      <a href="#">Services</a>
      <a href="#">Contact Us</a>
    </nav>
  </header>

  <section class="abs hero" role="img" aria-label="Photo of a pathologist in a white lab coat looking through a microscope in a bright laboratory">
    <div class="abs hero-circle">
      <div class="serif hero-title">BiscuitLab</div>
      <div class="hero-sub">NEXT GENERATION<br>PATHOLOGY CONSULTANTS</div>
      <div class="hero-text">LOREM IPSUM DOLOR SIT AMET CONSECT-<br>ETUR ADIPSICING ELIT.</div>
      <span class="btn-pill">READ MORE</span>
    </div>
  </section>

  <section class="abs band">
    <h2>FOCUS ON ITS PRECISION</h2>
    <p>Lorem ipsum dolor sit amet, consectetur adipisicing elit, sed do eiusmod tempor incididunt ut labore et dolore magna aliqua. Ut enim ad minim veniam, quis nostrud exercitation ullamco laboris nisi ut aliquip ex ea commodo consequat.</p>
    <div class="learn">Learn More
      <svg width="19" height="19" viewBox="0 0 19 19"><circle cx="9.5" cy="9.5" r="8.5" fill="none" stroke="#0b63ad" stroke-width="1.2"/><path d="M8 6l3.5 3.5L8 13" fill="none" stroke="#0b63ad" stroke-width="1.2"/></svg>
    </div>
  </section>

  <section class="abs feature" style="left:15px">
    <svg class="feature-icon" viewBox="0 0 47 47"><circle cx="23.5" cy="23.5" r="23.5" fill="#0a4f8f"/><circle cx="23.5" cy="14" r="4" fill="#fff"/><path d="M17 33c0-7 3-12 6.5-12s6.5 5 6.5 12z" fill="#fff"/><circle cx="21" cy="28" r="3" fill="#0a4f8f"/></svg>
    <h3 class="serif">Childhood Diseases</h3>
    <p>Lorem ipsum dolor sit amet cons-ectetur adipisicing elit eiusmod incididunt dolore magna aliqua.</p>
    <span class="more">Read More</span>
  </section>
  <section class="abs feature" style="left:256px">
    <svg class="feature-icon" viewBox="0 0 47 47"><circle cx="23.5" cy="23.5" r="23.5" fill="#0a4f8f"/><circle cx="23.5" cy="18" r="6" fill="#fff"/><path d="M12 34c0-7 5-10 11.5-10S35 27 35 34z" fill="#fff"/></svg>
    <h3 class="serif">Second Opinion</h3>
    <p>Lorem ipsum dolor sit amet cons-ectetur adipisicing elit eiusmod incididunt dolore magna aliqua.</p>
    <span class="more">Read More</span>
  </section>
  <section class="abs feature" style="left:497px">
    <svg class="feature-icon" viewBox="0 0 47 47"><circle cx="23.5" cy="23.5" r="23.5" fill="#0a4f8f"/><path d="M17 11c0 8 13 9 13 13s-13 5-13 13M30 11c0 8-13 9-13 13s13 5 13 13" fill="none" stroke="#fff" stroke-width="2"/><path d="M19 17h9M19 30h9" stroke="#fff" stroke-width="1.5"/></svg>
    <h3 class="serif">Dna Technology</h3>
    <p>Lorem ipsum dolor sit amet cons-ectetur adipisicing elit eiusmod incididunt dolore magna aliqua.</p>
    <span class="more">Read More</span>
  </section>

  <div class="abs rule" style="top:691px"></div>

  <section class="abs welcome">
    <h2 class="serif">Welcome to BISCUITLAB</h2>
    <p>Lorem ipsum dolor sit amet, consectetur adipisicing elit, sed do eiusmod tempor incididunt ut labore et dolore magna aliqua. Ut enim ad minim veniam, duis aute irure occaecat cupidatat non proident dolor in reprehenderit in voluptate velit esse cillum dolore eu fugiat nulla pariatur. Excepteur sint occaecat cupidatat non proident, ut enim ad minim veniam, quis nostrud exercitation ullamco laboris nisi ut sit amet, consectetur adipisicing elit...</p>
    <span class="btn-square" style="left:0;top:96px;width:59px;height:20px">Read More</span>
  </section>

  <section class="abs signup">
    <h2 class="serif">Sign Up New Account</h2>
    <div class="field" style="top:45px">Email address...</div>
    <div class="field" style="top:82px">Password...</div>
    <span class="btn-square" style="left:1px;top:114px;width:63px;height:22px;font-size:11px">Sign Up</span>
    <span class="forgot">Forgot your password?</span>
  </section>

  <div class="abs rule" style="top:869px"></div>

  <h2 class="abs serif services-title">ORDER SERVICES</h2>

  <section class="abs service" style="left:15px">
    <div class="service-photo" role="img" aria-label="Photo of a group of visitors gathered in a lab office" style="background:linear-gradient(135deg,#d9c7b0,#7a5a44)"></div>
    <h3 class="serif">Check Results/Reports</h3>
    <p>Lorem ipsum dolor sit amet, cons-ectetur adipisicing elit, sed do dolore magna aliqua...</p>
  </section>
  <section class="abs service" style="left:191px">
    <div class="service-photo" role="img" aria-label="Photo of two people working at microscopes in a dark lab" style="background:linear-gradient(135deg,#3a3a3a,#8c8780)"></div>
    <h3 class="serif">Access Our Educational Material/Webinars</h3>
    <p>Lorem ipsum dolor sit amet, cons-ectetur adipisicing elit, sed do dolore magna aliqua...</p>
  </section>
  <section class="abs service" style="left:366px">
    <div class="service-photo" role="img" aria-label="Photo of clinicians in white coats using lab equipment" style="background:linear-gradient(135deg,#b8a79a,#5e4a42)"></div>
    <h3 class="serif">Our Test Menu</h3>
    <p>Lorem ipsum dolor sit amet, cons-ectetur adipisicing elit, sed do dolore magna aliqua...</p>
  </section>
  <section class="abs service" style="left:542px">
    <div class="service-photo" role="img" aria-label="Photo of two pathologists talking in an office" style="background:linear-gradient(135deg,#6b5546,#cbbcae)"></div>
    <h3 class="serif">Speak With One Of The Pathologists</h3>
    <p>Lorem ipsum dolor sit amet, cons-ectetur adipisicing elit, sed do dolore magna aliqua...</p>
  </section>

  <footer class="abs footer">
    <span>Copyright © 2013 Biscuitlab.All Rights Reserved</span>
    <span>Privacy Policy &nbsp;|&nbsp; Terms of Uses</span>
  </footer>
</div>
</body>
</html>
```